We need a web page design for a new company called "Brambel". We provide an innovative music sharing mobile application that allows music listeners to share their music without paying for a monthly subscription. We would like to incorporate the attached logo and color scheme. The final design should communicate music gifting and sharing.

Industry/Entity Type

It Company

```html
<!DOCTYPE html>
<html lang="en">
<head>
<meta charset="utf-8">
<title>Brambel — Music Sharing</title>
<link rel="stylesheet" href="https://fonts.googleapis.com/css2?family=Open+Sans:wght@300;400;600;700&display=swap">
<style>
  :root {
    --brand-green: #5fa800;
    --white: #ffffff;
    --footer-bg: #2a2a2a;
    --footer-text: #9a9a9a;
    --hero-deep: #3b5a6a;
    --hero-mid: #7f9aa8;
    --hero-light: #c9d6dc;
    --store-dark: #222222;
    --store-light: #f2f2f2;
    --store-light-text: #444444;
  }
  * { box-sizing: border-box; margin: 0; padding: 0; }
  html, body { width: 1200px; height: 695px; overflow: hidden; }
  body { font-family: "Open Sans", Arial, sans-serif; color: var(--white); position: relative; background: var(--footer-bg); }

  .site-header { position: absolute; left: 0; top: 0; width: 1200px; height: 72px; background: var(--brand-green); }
  .brand { position: absolute; left: 15px; top: 19px; display: flex; align-items: center; gap: 8px; }
  .brand-mark { width: 28px; height: 28px; border-radius: 50%; background: var(--white); }
  .brand-name { font-size: 31px; font-weight: 600; line-height: 34px; color: var(--white); }

  .main-nav a, .footer-nav a { position: absolute; text-decoration: none; white-space: nowrap; }
  .main-nav a { top: 31px; font-size: 11.5px; color: var(--white); }
  .account-btn { position: absolute; top: 22px; width: 92px; height: 29px; border: 1px solid var(--white); border-radius: 2px; color: var(--white); font-size: 12px; display: flex; align-items: center; justify-content: center; }

  .hero { position: absolute; left: 0; top: 72px; width: 1200px; height: 552px; overflow: hidden; }
  .hero-photo { position: absolute; inset: 0; background:
      radial-gradient(ellipse 260px 300px at 960px 260px, #e6d3c6 0%, rgba(230,211,198,0) 70%),
      radial-gradient(ellipse 420px 300px at 260px 40px, rgba(220,230,235,0.6), rgba(220,230,235,0) 70%),
      linear-gradient(100deg, var(--hero-deep) 0%, var(--hero-mid) 45%, var(--hero-light) 75%, #e9eef0 100%); }
  .slider-prev { position: absolute; left: 41px; top: 230px; }
  .phone { position: absolute; left: 123px; top: 99px; width: 173px; height: 367px; border-radius: 26px; background: linear-gradient(180deg, #f4f4f4, #d9d9d9); }
  .phone-screen { position: absolute; left: 6px; top: 46px; width: 161px; height: 273px; border-radius: 3px; background: linear-gradient(180deg, #2d2d2d, #111); }

  .hero-copy { position: absolute; left: 339px; top: 112px; width: 360px; }
  .hero-title { font-size: 34px; font-weight: 700; letter-spacing: 1px; line-height: 40px; }
  .hero-subtitle { margin-top: 12px; font-size: 25.5px; font-weight: 300; line-height: 34px; }
  .hero-text { margin-top: 12px; font-size: 10.3px; line-height: 20px; font-weight: 400; }
  .subscribe-btn { position: absolute; left: 339px; top: 318px; width: 173px; height: 46px; border: 1px solid var(--white); font-size: 13.5px; font-weight: 600; display: flex; align-items: center; justify-content: center; }
  .store-btn { position: absolute; top: 388px; width: 164px; height: 54px; display: flex; align-items: center; gap: 12px; padding-left: 20px; border-radius: 2px; }
  .store-btn .store-icon { width: 24px; height: 24px; border-radius: 50%; }
  .store-btn small { display: block; font-size: 11px; line-height: 15px; }
  .store-btn strong { display: block; font-size: 11.5px; font-weight: 600; line-height: 16px; }
  .store-app { left: 339px; background: var(--store-dark); color: var(--white); }
  .store-app .store-icon { background: var(--white); }
  .store-play { left: 517px; background: var(--store-light); color: var(--store-light-text); }
  .store-play .store-icon { background: #6ab04c; }

  .site-footer { position: absolute; left: 0; top: 624px; width: 1200px; height: 71px; background: var(--footer-bg); }
  .footer-nav a { top: 30px; font-size: 11px; color: var(--footer-text); }
  .copyright { position: absolute; left: 664px; top: 30px; font-size: 10px; color: var(--footer-text); white-space: nowrap; }
  .social { position: absolute; top: 31px; width: 11px; height: 11px; border-radius: 50%; background: var(--footer-text); }
</style>
</head>
<body>
  <header class="site-header">
    <div class="brand">
      <span class="brand-mark"></span>
      <span class="brand-name">Brambel</span>
    </div>
    <nav class="main-nav">
      <a style="left:350px">HOME</a>
      <a style="left:447px">ABOUT US</a>
      <a style="left:566px">SERVICES</a>
      <a style="left:677px">MUSICS</a>
      <a style="left:782px">SHARING</a>
      <a style="left:893px">CONTACT US</a>
    </nav>
    <a class="account-btn" style="left:986px">SIGN IN</a>
    <a class="account-btn" style="left:1089px">SIGN UP</a>
  </header>

  <section class="hero">
    <div class="hero-photo" role="img" aria-label="Blurred blue-grey background with a smiling man in sunglasses and headphones on the right"></div>
    <svg class="slider-prev" width="24" height="76" viewBox="0 0 24 76" aria-hidden="true">
      <polyline points="22,2 2,38 22,74" fill="none" stroke="rgba(255,255,255,0.45)" stroke-width="1.2"/>
    </svg>
    <div class="phone" role="img" aria-label="White smartphone showing the music player app">
      <div class="phone-screen"></div>
    </div>
    <div class="hero-copy">
      <h1 class="hero-title">BRAMBEL</h1>
      <p class="hero-subtitle">IT IS MUSIC SHARING SHARING AND GIFTING TOTALLY FREE</p>
      <p class="hero-text">WE HAVE A MUSIC SHARING MOBILE APPLICATION THAT ALLOWS MUSIC LISTENERS TO SHARE THEIR MUSIC WITHOUT PAYING FOR A MONTHLY SUBSCRIPTION.</p>
    </div>
    <a class="subscribe-btn">SUBSCRIBE NOW</a>
    <a class="store-btn store-app"><span class="store-icon"></span><span><small>Download it from</small><strong>APP MARKET</strong></span></a>
    <a class="store-btn store-play"><span class="store-icon"></span><span><small>Download it from</small><strong>PLAY DEPOT</strong></span></a>
  </section>

  <footer class="site-footer">
    <nav class="footer-nav">
      <a style="left:99px">HOME</a>
      <a style="left:166px">ABOUT US</a>
      <a style="left:254px">SERVICES</a>
      <a style="left:336px">MUSICS</a>
      <a style="left:410px">SHARING</a>
      <a style="left:492px">CONTACT US</a>
    </nav>
    <p class="copyright">COPYRIGHT © 2014 · BRAMBEL · ALL RIGHTS RESERVED</p>
    <span class="social" style="left:940px"></span>
    <span class="social" style="left:973px"></span>
    <span class="social" style="left:1008px"></span>
    <span class="social" style="left:1042px"></span>
    <span class="social" style="left:1076px"></span>
    <span class="social" style="left:1111px"></span>
  </footer>
</body>
</html>
```